Larkmoor Drones Business Card

We are a new company based in Central Queensland, Australia that uses specalised drones (Voskel Ferra Q80) to undertake mainly agricultural operations, like spraying weeds, spraying crops, spreading seed etc. I have attached a Plimbo proof of a card I was thinking along the lines of - purely a start point. The drone used in the business card MUST be a Voskel Ferra Q80.
I am very open to other ideas, especially fonts and layout. I don't have website etc set up yet.
The images are stock and easily interchangeable, I just ask that any background images reflect the local central Queensland area. The photo of the drone is not even complete (propellers cut off) and I need a new stock photo – I’m not sure if this is an issue, or I can pay for an image if need be. PLEASE FIND AN FERRA Q80 image - 4 sprayers, not 6.
The logo/business name is very draft and looking for further ideas, ideally incorporating drones or agriculture design elements into the design of the business name. The business name needs work on the graphic/design – it is a draft that I have included, the drone propellers (being a different colour) are DRAFT only and intended for changes. PLEASE DO NOT USE THE DRONE PORPELLER I HAVE USED AS A DRAFT. TRY TO FIND SOMETHING ELSE.. The arrow is a shape and not aligned in any way, I would also like ideas on different fonts and additional elements, like air streams, aviation elements, aviation or country western (farming like) themes and fonts etc.
Ideally looking at staying within the blue, green and yellow colours, keeping with an natural, outdoorsy, environmental feel.

Target Market(s)

Farmers, Agriculture, Local Governments, Land Managers

Industry/Entity Type

Agriculture, Drones, Aviation

Contact Information for Business Card

Agricultural Drone (Voskel Ferra Q80), Farming, Business Name.

Font styles to use
Sans Serif

Colors
0054AA
0677BA
7BADD7
CADEEF
E8F1F8
0094D4
00A9DD
6FCCEA
C7EBF8
E9F6FB
00AB8E
00BBA5
67D7C9
C6EFE9
E9F9F6
59FF00
82FF00
B8FF75
E3FFCB
F4FFEA

Requirements
Must have
• Voskel Ferra Q80 Drone
Should not have
• Tractors

```html
<!DOCTYPE html>
<html lang="en">
<head>
<meta charset="utf-8">
<title>Larkmoor Drones – Business Card</title>
<link rel="stylesheet" href="https://fonts.googleapis.com/css2?family=Poppins:wght@400;600;700&family=Exo+2:wght@800&display=swap">
<style>
  :root {
    --backdrop: #808080;
    --paper: #ffffff;
    --ink: #222222;
    --field-green: #3a9607;
    --sky-top: #9cc3e6;
    --sky-low: #dfe9f3;
    --crop: #4e7a2a;
    --crop-dark: #2f4d17;
    --drone-sky: #dce8f6;
    --grass: #6fbf2e;
    --cloud: #eef3f8;
  }
  * { margin: 0; padding: 0; box-sizing: border-box; }
  html, body { width: 935px; height: 1200px; overflow: hidden; }
  body { background: var(--backdrop); position: relative; font-family: "Poppins", sans-serif; }
  .card {
    position: absolute; left: 161px; width: 613px; height: 350px;
    background: var(--paper); overflow: hidden;
    box-shadow: 8px 14px 22px rgba(0,0,0,0.35);
  }
  .card--front { top: 175px; }
  .card--back { top: 672px; }
  .card svg.art { position: absolute; inset: 0; }
  .brand {
    position: absolute; display: flex; align-items: center; gap: 8px;
    font-family: "Poppins", sans-serif; font-weight: 700; color: var(--ink);
    white-space: nowrap;
  }
  .brand__dot { width: 14px; height: 14px; border-radius: 50%; background: var(--field-green); }
  .card--front .brand { left: 32px; top: 72px; font-size: 29px; }
  .card--back .brand { left: 43px; top: 52px; font-size: 22px; }
  .card--back .brand__dot { width: 11px; height: 11px; }
  .services { position: absolute; left: 33px; top: 150px; list-style: none; }
  .services li {
    display: flex; align-items: center; gap: 10px; height: 39px;
    color: #fff; font-weight: 700; font-size: 19px; letter-spacing: 0.2px;
  }
  .services svg { width: 22px; height: 22px; }
  .front-url { position: absolute; left: 32px; top: 293px; font-size: 21px; color: var(--ink); }
  .person { position: absolute; left: 42px; top: 107px; color: var(--ink); }
  .person__name { font-family: "Exo 2", sans-serif; font-weight: 800; font-size: 29px; line-height: 1; letter-spacing: 0.5px; }
  .person__role { font-weight: 600; font-size: 18px; line-height: 1.2; margin-top: 3px; }
  .contacts { position: absolute; left: 44px; top: 198px; width: 211px; list-style: none; }
  .contacts li {
    display: flex; align-items: center; gap: 9px; height: 37px;
    color: #fff; font-size: 13.5px; border-bottom: 1px solid rgba(255,255,255,0.7);
    white-space: nowrap;
  }
  .contacts li:last-child { border-bottom: none; }
  .contacts .icon { width: 20px; height: 20px; border-radius: 50%; background: var(--ink); display: grid; place-items: center; flex: none; }
  .contacts .icon svg { width: 11px; height: 11px; }
</style>
</head>
<body>

<section class="card card--front">
  <svg class="art" width="613" height="350" viewBox="0 0 613 350">
    <defs>
      <linearGradient id="landscape" x1="0" y1="0" x2="0" y2="1">
        <stop offset="0" stop-color="var(--sky-top)"/>
        <stop offset="0.45" stop-color="var(--sky-low)"/>
        <stop offset="0.62" stop-color="#6f8a55"/>
        <stop offset="1" stop-color="var(--crop)"/>
      </linearGradient>
      <linearGradient id="rows" x1="0" y1="0" x2="1" y2="1">
        <stop offset="0" stop-color="var(--crop)"/>
        <stop offset="1" stop-color="var(--crop-dark)"/>
      </linearGradient>
    </defs>
    <polygon points="0,128 330,128 345,276 0,276" fill="var(--field-green)"/>
    <g role="img" aria-label="Central Queensland farmland under a cloudy sky">
      <polygon points="410,0 613,0 613,283 360,68" fill="url(#landscape)"/>
    </g>
    <g role="img" aria-label="Voskel Ferra Q80 spray drone in flight against pale sky">
      <polygon points="356,86 463,193 356,300 249,193" fill="var(--drone-sky)" stroke="var(--drone-sky)" stroke-width="14" stroke-linejoin="round"/>
    </g>
    <g role="img" aria-label="Aerial view of crop rows">
      <polygon points="480,193 601,289 490,400 374,314" fill="url(#rows)" stroke="var(--crop)" stroke-width="10" stroke-linejoin="round"/>
      <polygon points="590,350 613,325 613,350" fill="var(--crop)"/>
    </g>
  </svg>
  <div class="brand"><span class="brand__dot"></span>Larkmoor Drones</div>
  <ul class="services">
    <li><svg viewBox="0 0 24 24" fill="none" stroke="#fff" stroke-width="2.6"><path d="M14 3H3v18h18v-9"/><path d="M7 11l4 4 10-11"/></svg>SPRAYING WEEDS</li>
    <li><svg viewBox="0 0 24 24" fill="none" stroke="#fff" stroke-width="2.6"><path d="M14 3H3v18h18v-9"/><path d="M7 11l4 4 10-11"/></svg>SPRAYING CROPS</li>
    <li><svg viewBox="0 0 24 24" fill="none" stroke="#fff" stroke-width="2.6"><path d="M14 3H3v18h18v-9"/><path d="M7 11l4 4 10-11"/></svg>SPREADING SEED</li>
  </ul>
  <p class="front-url">www.larkmoordrones.com.au</p>
</section>

<section class="card card--back">
  <svg class="art" width="613" height="350" viewBox="0 0 613 350">
    <defs>
      <linearGradient id="sky-field" x1="0" y1="0" x2="0" y2="1">
        <stop offset="0" stop-color="#8fb9e3"/>
        <stop offset="0.3" stop-color="var(--cloud)"/>
        <stop offset="0.52" stop-color="#cbd8e4"/>
        <stop offset="0.6" stop-color="#7fb64a"/>
        <stop offset="1" stop-color="var(--grass)"/>
      </linearGradient>
      <linearGradient id="fade" x1="0" y1="0" x2="1" y2="0">
        <stop offset="0" stop-color="#fff" stop-opacity="1"/>
        <stop offset="0.4" stop-color="#fff" stop-opacity="0"/>
      </linearGradient>
    </defs>
    <g role="img" aria-label="Voskel Ferra Q80 spray drone flying over green Queensland paddock">
      <polygon points="262,0 613,0 613,350 212,350 421,173" fill="url(#sky-field)"/>
      <polygon points="262,0 613,0 613,180 421,173" fill="url(#fade)"/>
    </g>
    <polygon points="0,179 408,179 218,350 0,350" fill="var(--field-green)"/>
    <g class="photo-frame" stroke="#fff" stroke-linecap="square">
      <line x1="226" y1="352" x2="615" y2="-2" stroke-width="6"/>
      <line x1="421" y1="173" x2="601" y2="352" stroke-width="6"/>
      <line x1="262" y1="0" x2="421" y2="173" stroke-width="2" opacity="0.85"/>
    </g>
  </svg>
  <div class="brand"><span class="brand__dot"></span>Larkmoor Drones</div>
  <div class="person">
    <p class="person__name">TOM HADLEY</p>
    <p class="person__role">Manager</p>
  </div>
  <ul class="contacts">
    <li><span class="icon"><svg viewBox="0 0 24 24" fill="#fff"><path d="M6.6 10.8a15 15 0 0 0 6.6 6.6l2.2-2.2a1 1 0 0 1 1-.25 11.4 11.4 0 0 0 3.6.57 1 1 0 0 1 1 1V20a1 1 0 0 1-1 1A17 17 0 0 1 3 4a1 1 0 0 1 1-1h3.5a1 1 0 0 1 1 1c0 1.25.2 2.45.57 3.57a1 1 0 0 1-.25 1z"/></svg></span>0749 512 630</li>
    <li><span class="icon"><svg viewBox="0 0 24 24" fill="none" stroke="#fff" stroke-width="2.4"><rect x="3" y="5" width="18" height="14"/><path d="M3 6l9 7 9-7"/></svg></span>hello@larkmoordrones.com.au</li>
    <li><span class="icon"><svg viewBox="0 0 24 24" fill="none" stroke="#fff" stroke-width="2"><circle cx="12" cy="12" r="9"/><path d="M3 12h18M12 3c3 3 3 15 0 18M12 3c-3 3-3 15 0 18"/></svg></span>www.larkmoordrones.com.au</li>
  </ul>
</section>

</body>
</html>
```